food delivery web site design

Currently we have a smartphone app (ios/android) that is being used by our clients to make orders to about 30 different restaurants.

We would like to extent this and have also a website that is able to mimic the same functionalities:
- register
- show restaurants based on the selected address
- make order to an restaurant
- being able to process orders for other registered users (please read the attached doc for complete info on this)

Take a look at the attached doc for more info.

```html
<!DOCTYPE html>
<html lang="ro">
<head>
<meta charset="utf-8">
<title>Gustino – Validare adresă</title>
<link href="https://fonts.googleapis.com/css2?family=Bebas+Neue&family=Open+Sans:wght@400;600&display=swap" rel="stylesheet">
<style>
  :root{
    --red:#9b1a0c;
    --red-dark:#7e1206;
    --yellow:#f3c84b;
    --ink:#231f20;
    --grey-title:#c8c8c8;
    --grey-text:#666666;
    --grey-label:#999999;
    --grey-btn:#666666;
    --rule:#d6d6d6;
    --footer:#1d1d1d;
    --pattern-light:#ececec;
    --map-base:#e8e4dc;
    --map-road:#f6d66b;
    --white:#ffffff;
  }
  *{box-sizing:border-box;margin:0;padding:0}
  html,body{width:1200px;height:831px;overflow:hidden;background:var(--white)}
  body{font-family:'Open Sans',Arial,sans-serif;color:var(--grey-text)}
  .page{position:relative;width:1200px;height:831px;overflow:hidden}

  .food-pattern{position:absolute;left:0;top:0;width:1200px;height:50px;
    background:linear-gradient(180deg,#f7f7f7,var(--pattern-light))}
  .header-band{position:absolute;left:0;top:50px;width:1200px;height:54px;background:var(--red);
    border-top:2px solid var(--red-dark);border-bottom:2px solid var(--red-dark)}
  .header-band::after{content:"";position:absolute;left:0;right:0;bottom:3px;height:1px;background:rgba(255,255,255,.35)}
  .header-rule{position:absolute;top:27px;height:3px;border-top:1px solid rgba(255,255,255,.55);border-bottom:1px solid rgba(255,255,255,.55)}
  .header-rule.left{left:297px;width:36px}
  .header-rule.dotted{left:610px;width:276px;border:0;border-top:2px dotted rgba(255,255,255,.55)}
  .header-rule.right{left:1064px;width:136px}

  .logo-badge{position:absolute;left:138px;top:0;width:160px;height:158px}
  .logo-name{position:absolute;left:0;top:62px;width:160px;text-align:center;
    font-family:'Bebas Neue',Impact,sans-serif;font-size:30px;color:var(--red)}

  .call{position:absolute;left:350px;top:62px;font-family:'Bebas Neue',Impact,sans-serif;
    font-size:30px;color:var(--white);letter-spacing:.2px;display:flex;align-items:center;gap:6px}
  .call .number{color:var(--yellow);display:flex;align-items:center;gap:4px}
  .account{position:absolute;top:66px;display:flex;align-items:center;gap:6px;
    font-family:'Bebas Neue',Impact,sans-serif;font-size:19px;color:var(--white)}
  .account.login{left:906px}
  .account.signin{left:981px}

  .page-title{position:absolute;left:138px;top:232px;font-family:'Bebas Neue',Impact,sans-serif;
    font-size:56px;line-height:1;color:var(--grey-title);letter-spacing:.5px}
  .title-rule{position:absolute;left:138px;top:296px;width:924px;height:1px;background:var(--rule)}

  .address{position:absolute;left:139px;top:331px;width:330px;font-size:17px;line-height:23px;color:var(--grey-text)}
  .address .label{font-family:'Bebas Neue',Impact,sans-serif;font-size:22px;color:var(--grey-label);margin-right:4px}

  .question{position:absolute;left:138px;top:437px;font-family:'Bebas Neue',Impact,sans-serif;
    font-size:34px;line-height:1;color:var(--grey-text);letter-spacing:.3px}
  .btn{position:absolute;top:505px;width:67px;height:41px;display:flex;align-items:center;justify-content:center;
    font-family:'Bebas Neue',Impact,sans-serif;font-size:28px;color:var(--white)}
  .btn.yes{left:138px;background:var(--red)}
  .btn.no{left:223px;background:var(--grey-btn)}

  .map{position:absolute;left:609px;top:334px;width:453px;height:263px;border:1px solid #cfcfcf;
    background:linear-gradient(160deg,#ece8e0 0%,var(--map-base) 60%,#e2ddd3 100%);overflow:hidden}

  .footer{position:absolute;left:0;top:775px;width:1200px;height:56px;background:var(--footer)}
  .footer-links{position:absolute;left:138px;top:18px;display:flex;font-size:13px;color:var(--white)}
  .footer-links span{padding:0 10px;border-left:1px solid #555}
  .footer-links span:first-child{padding-left:0;border-left:0}
  .copyright{position:absolute;right:138px;top:18px;font-size:13px;color:var(--white)}
</style>
</head>
<body>
<div class="page">
  <div class="food-pattern" role="img" aria-label="Decorative band of line-drawn food doodles"></div>
  <div class="header-band">
    <div class="header-rule left"></div>
    <div class="header-rule dotted"></div>
    <div class="header-rule right"></div>
  </div>

  <div class="logo-badge">
    <svg width="160" height="158" viewBox="0 0 160 158">
      <path d="M2 0 H158 V130 L136 152 H24 L2 130 Z" fill="var(--ink)"/>
      <path d="M8 0 V127 L27 146 H133 L152 127 V0" fill="none" stroke="#8a7f7c" stroke-width="1"/>
      <circle cx="80" cy="78" r="56" fill="#ffffff"/>
      <circle cx="80" cy="80" r="46" fill="#eeeeee"/>
    </svg>
    <div class="logo-name">Gustino</div>
  </div>

  <div class="call">SUNĂ-NE LA
    <span class="number">
      <svg width="16" height="20" viewBox="0 0 16 20"><path d="M4 1 L7 5 L5 8 Q7 12 10 14 L12 12 L15 16 L12 19 Q3 15 1 4 Z" fill="var(--yellow)"/></svg>
      0700 123 456
    </span>
  </div>
  <div class="account login">
    <svg width="15" height="14" viewBox="0 0 15 14"><path d="M1 13 V8 Q1 5 5 5 H9 V1 L14 6.5 L9 12 V8 H5 Q4 8 4 9 V13 Z" fill="#fff"/></svg>
    LOGIN
  </div>
  <div class="account signin">
    <svg width="16" height="14" viewBox="0 0 16 14"><circle cx="6" cy="4" r="3.2" fill="#fff"/><path d="M0 13 Q0 8 6 8 Q12 8 12 13 Z" fill="#fff"/><path d="M12 1 V6 M9.5 3.5 H14.5" stroke="#fff" stroke-width="1.6"/></svg>
    SIGN IN
  </div>

  <h1 class="page-title">VALIDARE ADRESĂ</h1>
  <div class="title-rule"></div>

  <p class="address"><span class="label">ADRESA:</span>Lorem ipsum dolor sit amet, consectetur adipiscing elit</p>

  <h2 class="question">ESTE CORECTĂ ADRESA DE PE HARTĂ&nbsp; ?</h2>
  <a class="btn yes">DA</a>
  <a class="btn no">NU</a>

  <div class="map" role="img" aria-label="Street map showing the delivery address with a location pin"></div>

  <footer class="footer" role="img" aria-label="Dark footer with faint food doodle pattern">
    <nav class="footer-links">
      <span>Contactează-ne</span><span>Despre noi</span><span>Partenerii noștri</span><span>FAQ</span><span>Devino partener</span>
    </nav>
    <div class="copyright">Copyright © 2013 gustino.ro. Toate drepturile rezervate.</div>
  </footer>
</div>
</body>
</html>
```